Business card design for a dynamic IT consulting company

We need a business card design for a young firm, specialized in the Telecommunications/Consulting industry. The name of the company is Quindor and Partners Business Consulting Ltd. (Short name: Quindor and Partnes)
Quindor = solve read reverse, so we aim to be uncomplicated and solution-oriented. The small pipe in our logo is also related to the word solve. So we need a new business card design, which is simple, eye catching and something non traditional (I would probably prefer a square shaped design rather than a rectangle, but open for suggestions). Attached our logo.

Target Market(s)

Usually our customers are Tier1 Telecoms providers (Q-Netra, Palorix, etc) and their executives.

Industry/Entity Type

Business

Contact Information for Business Card

Name: Bence Tolnavari
Email: b.tolnavari@quindor.hu
Web: www.quindor.hu
Mobile: +36 30 518 2769
Title: Managing Director

Optional:
Company name: Quindor and Partners Ltd.
Address: 1087 Budapest, Tolvenka str. 28/C, Hungary

Font styles to use
Other font styles liked:
• helveticaneue_medium, Prime Regular are used now.

Colors

Designer to choose colors to be used in the design.

Requirements
Must have
• I would like to have a 2 sided design.
Nice to have
• I thought if we make the logo a bit bigger (without the company name), that could go to the back with the company name below. I though, if the pipe in the logo is somehow touchable on the business card, would be nice and unique.

```html
<!DOCTYPE html>
<html lang="en">
<head>
<meta charset="utf-8">
<title>Quindor and Partners – Business Card</title>
<link rel="stylesheet" href="https://fonts.googleapis.com/css2?family=Roboto:wght@300;400;500&display=swap">
<style>
  :root {
    --backdrop: #a3a3a3;
    --card-black: #1c1c1d;
    --card-white: #f7f7f7;
    --ink: #4a4a4a;
    --ink-soft: #6d6d6d;
    --logo-grey: #c9c9c9;
    --blue: #1f8fd1;
    --magenta: #b3268f;
    --stripe-grey: #5c5c5c;
    --rule: #9d9d9d;
  }
  * { margin: 0; padding: 0; box-sizing: border-box; }
  html, body { width: 1200px; height: 900px; overflow: hidden; }
  body {
    background: var(--backdrop);
    font-family: "Roboto", Arial, sans-serif;
    display: flex;
    flex-direction: column;
    align-items: center;
    justify-content: center;
    gap: 46px;
  }
  .card {
    width: 660px;
    height: 377px;
    border-radius: 20px;
    position: relative;
    overflow: hidden;
    box-shadow: 0 10px 24px rgba(0,0,0,0.28);
  }

  /* Back side */
  .card-back {
    background: var(--card-black);
    display: flex;
    flex-direction: column;
    align-items: center;
    justify-content: center;
    gap: 34px;
  }
  .brand {
    display: flex;
    align-items: center;
    gap: 14px;
  }
  .brand-square {
    width: 26px;
    height: 26px;
    background: var(--blue);
  }
  .brand-name {
    font-weight: 300;
    color: var(--logo-grey);
    letter-spacing: 0.5px;
  }
  .card-back .brand-name { font-size: 46px; }
  .back-web {
    color: var(--logo-grey);
    font-size: 15px;
    letter-spacing: 0.3px;
  }

  /* Front side */
  .card-front {
    background: linear-gradient(160deg, #ffffff 0%, var(--card-white) 55%, #ececec 100%);
  }
  .front-strip {
    position: absolute;
    left: 0; top: 0; bottom: 0;
    width: 150px;
    background: var(--card-black);
  }
  .strip-brand {
    position: absolute;
    left: 75px;
    top: 188px;
    transform: translate(-50%, -50%) rotate(-90deg);
    white-space: nowrap;
  }
  .strip-brand .brand-name { font-size: 30px; }
  .strip-brand .brand-square { width: 18px; height: 18px; }
  .accent-bar {
    position: absolute;
    left: 158px;
    width: 6px;
  }
  .accent-blue { top: 0; height: 126px; background: var(--blue); }
  .accent-magenta { top: 126px; height: 126px; background: var(--magenta); }
  .accent-grey { top: 252px; height: 125px; background: var(--stripe-grey); }

  .front-content {
    position: absolute;
    left: 196px;
    right: 26px;
    top: 0; bottom: 0;
  }
  .person-name {
    position: absolute;
    top: 52px;
    font-size: 34px;
    font-weight: 500;
    letter-spacing: 0.2px;
  }
  .first-name { color: var(--blue); }
  .last-name { color: var(--magenta); font-weight: 400; }
  .person-title {
    position: absolute;
    top: 96px;
    font-size: 19px;
    color: var(--ink);
  }
  .rule {
    position: absolute;
    left: 0; right: 8px;
    height: 1px;
    background: var(--rule);
  }
  .rule-top { top: 140px; }
  .rule-bottom { top: 290px; }
  .company {
    position: absolute;
    top: 222px;
  }
  .company-name {
    font-size: 16px;
    font-weight: 500;
    color: var(--blue);
  }
  .company-address {
    font-size: 16px;
    color: var(--ink-soft);
    margin-top: 4px;
  }
  .contacts {
    position: absolute;
    top: 308px;
    left: 0; right: 0;
    display: flex;
    justify-content: flex-start;
    align-items: center;
    gap: 22px;
  }
  .contact-item {
    display: flex;
    align-items: center;
    gap: 7px;
    font-size: 13px;
    color: var(--ink-soft);
    white-space: nowrap;
  }
  .contact-icon {
    flex: none;
    width: 19px; height: 19px;
    border-radius: 3px;
    display: flex;
    align-items: center;
    justify-content: center;
  }
  .icon-phone { background: var(--blue); }
  .icon-mail { background: var(--magenta); }
  .icon-web { background: var(--stripe-grey); }
</style>
</head>
<body>

  <section class="card card-back" aria-label="Back of business card">
    <div class="brand">
      <span class="brand-square"></span>
      <span class="brand-name">Quindor &amp; Partners</span>
    </div>
    <p class="back-web">www.quindor.hu</p>
  </section>

  <section class="card card-front" aria-label="Front of business card">
    <div class="front-strip">
      <div class="strip-brand brand">
        <span class="brand-square"></span>
        <span class="brand-name">Quindor &amp; Partners</span>
      </div>
    </div>
    <span class="accent-bar accent-blue"></span>
    <span class="accent-bar accent-magenta"></span>
    <span class="accent-bar accent-grey"></span>

    <div class="front-content">
      <h1 class="person-name"><span class="first-name">Bence</span> <span class="last-name">Tolnavari</span></h1>
      <p class="person-title">Managing Director</p>
      <span class="rule rule-top"></span>

      <div class="company">
        <p class="company-name">Quindor and Partners Ltd</p>
        <p class="company-address">1087 Budapest, Tolvenka str. 28/C, Hungary</p>
      </div>
      <span class="rule rule-bottom"></span>

      <div class="contacts">
        <div class="contact-item">
          <span class="contact-icon icon-phone">
            <svg width="12" height="12" viewBox="0 0 24 24"><path fill="#fff" d="M6.6 10.8a15.1 15.1 0 0 0 6.6 6.6l2.2-2.2c.3-.3.7-.4 1-.2 1.1.4 2.300.6 3.6.6.6 0 1 .4 1 1V20c0 .6-.4 1-1 1A17 17 0 0 1 3 4c0-.6.4-1 1-1h3.5c.6 0 1 .4 1 1 0 1.3.2 2.5.6 3.6.1.3 0 .7-.2 1z"/></svg>
          </span>
          <span>+36 30 518 2769</span>
        </div>
        <div class="contact-item">
          <span class="contact-icon icon-mail">
            <svg width="12" height="10" viewBox="0 0 24 18"><rect x="1" y="1" width="22" height="16" rx="1.5" fill="none" stroke="#fff" stroke-width="2"/><path d="M2 2l10 8 10-8" fill="none" stroke="#fff" stroke-width="2"/></svg>
          </span>
          <span>b.tolnavari@quindor.hu</span>
        </div>
        <div class="contact-item">
          <span class="contact-icon icon-web">
            <svg width="12" height="12" viewBox="0 0 24 24"><circle cx="12" cy="12" r="10" fill="none" stroke="#fff" stroke-width="2"/><ellipse cx="12" cy="12" rx="4.5" ry="10" fill="none" stroke="#fff" stroke-width="1.6"/><path d="M2 12h20" stroke="#fff" stroke-width="1.6"/></svg>
          </span>
          <span>www.quindor.hu</span>
        </div>
      </div>
    </div>
  </section>

</body>
</html>
```